Business card design

Hi,
I need to have a business card design based on the current logo.
If competitive I not put it out to everyone.

It can be single of double sided

Target Market(s)

Food businesses

Industry/Entity Type

Food Manufacturing

Contact Information for Business Card

Details will on card will be as follows Name = Marcus Bell Email = Marcus@PanHearth.com.au Phone = 0418563207 Address = 57 Larkin Street , Fortitude Valley QLD 4006 Australia

Font styles to use
Other font styles liked:
• based on two fonts - Adelle & Museo

Requirements
Must have
• Based on the on switch concept

```html
<!DOCTYPE html>
<html lang="en">
<head>
<meta charset="utf-8">
<title>PanHearth Business Card</title>
<link rel="stylesheet" href="https://fonts.googleapis.com/css2?family=Arimo:wght@400;700&family=Zilla+Slab:wght@500;600&display=swap">
<style>
  :root {
    --bg: #2b2b2b;
    --brand-red: #ec2a4a;
    --card-white: #ffffff;
    --ink: #2d2426;
    --rule: #ec2a4a;
  }
  * { box-sizing: border-box; margin: 0; padding: 0; }
  html, body {
    width: 1200px; height: 1015px; overflow: hidden;
    background: var(--bg);
  }
  .canvas {
    width: 1200px; height: 1015px;
    display: flex; flex-direction: column; align-items: center; justify-content: center;
    gap: 45px;
  }
  .card {
    width: 700px; height: 400px;
    position: relative;
    box-shadow: 0 8px 24px rgba(0,0,0,.45);
  }
  .card--front { background: var(--brand-red); }
  .card--back { background: var(--card-white); }

  .wordmark { position: absolute; }
  .wordmark__name {
    font-family: "Arimo", Arial, sans-serif;
    font-weight: 700;
    letter-spacing: 2px;
    line-height: 1;
    display: flex; align-items: center; gap: 14px;
  }
  .wordmark__dot {
    width: 34px; height: 34px; border-radius: 50%; display: inline-block;
  }
  .wordmark__tagline {
    font-family: "Zilla Slab", Georgia, serif;
    font-weight: 600;
    font-size: 17px;
    letter-spacing: .6px;
    margin-top: 6px;
    margin-left: 48px;
  }

  .card--front .wordmark { left: 0; right: 0; top: 160px; display: flex; flex-direction: column; align-items: center; }
  .card--front .wordmark__name { font-size: 50px; color: var(--card-white); }
  .card--front .wordmark__dot { background: var(--card-white); }
  .card--front .wordmark__tagline { color: var(--card-white); }

  .card--back .wordmark { right: 60px; top: 60px; }
  .card--back .wordmark__name { font-size: 46px; color: var(--ink); }
  .card--back .wordmark__dot { background: var(--brand-red); }
  .card--back .wordmark__tagline { color: var(--ink); }

  .rule { position: absolute; height: 1px; background: var(--rule); }
  .rule--top { right: 60px; top: 160px; width: 360px; }
  .rule--name { left: 60px; top: 262px; width: 330px; }

  .address {
    position: absolute; right: 60px; top: 178px;
    font-family: "Arimo", Arial, sans-serif; font-style: normal; font-size: 20px; line-height: 1.25;
    color: var(--ink); text-align: right;
  }
  .person {
    position: absolute; left: 60px; top: 226px;
    font-family: "Arimo", Arial, sans-serif; font-weight: 700; font-size: 30px;
    letter-spacing: 1px; color: var(--brand-red);
  }
  .contacts {
    position: absolute; left: 60px; top: 276px; list-style: none;
    font-family: "Arimo", Arial, sans-serif; font-size: 21px; color: var(--ink);
  }
  .contacts li { display: flex; align-items: center; gap: 12px; height: 30px; }
  .contacts svg { width: 20px; height: 20px; flex: none; }
</style>
</head>
<body>
<main class="canvas">
  <section class="card card--front" aria-label="Card front">
    <div class="wordmark">
      <div class="wordmark__name"><span class="wordmark__dot"></span>PANHEARTH</div>
      <div class="wordmark__tagline">Kitchen Supply Made Simple</div>
    </div>
  </section>

  <section class="card card--back" aria-label="Card back">
    <div class="wordmark">
      <div class="wordmark__name"><span class="wordmark__dot"></span>PANHEARTH</div>
      <div class="wordmark__tagline">Kitchen Supply Made Simple</div>
    </div>
    <div class="rule rule--top"></div>
    <address class="address">57 Larkin Street<br>Marlow Heights<br>QLD 4172 Australia</address>

    <h1 class="person">MARCUS BELL</h1>
    <div class="rule rule--name"></div>
    <ul class="contacts">
      <li>
        <svg viewBox="0 0 24 24" aria-hidden="true"><path fill="var(--brand-red)" d="M6.6 10.8a15.1 15.1 0 0 0 6.6 6.6l2.2-2.2c.3-.3.7-.4 1-.2 1.1.4 2.3.6 3.6.6.6 0 1 .4 1 1V20c0 .6-.4 1-1 1A17 17 0 0 1 3 4c0-.6.4-1 1-1h3.5c.6 0 1 .4 1 1 0 1.3.2 2.5.6 3.6.1.3 0 .7-.2 1z"/></svg>
        0418563207
      </li>
      <li>
        <svg viewBox="0 0 24 24" aria-hidden="true"><rect x="2" y="5" width="20" height="14" fill="var(--brand-red)"/><path d="M2 5l10 8 10-8" fill="none" stroke="#fff" stroke-width="1.6"/></svg>
        Marcus@PanHearth.com.au
      </li>
      <li>
        <svg viewBox="0 0 24 24" aria-hidden="true"><g fill="none" stroke="var(--brand-red)" stroke-width="1.8"><circle cx="12" cy="12" r="9.5"/><ellipse cx="12" cy="12" rx="4" ry="9.5"/><path d="M2.5 12h19M4 7h16M4 17h16"/></g></svg>
        www.PanHearth.com.au
      </li>
    </ul>
  </section>
</main>
</body>
</html>
```